Lumavento business card

We need a modern business card - With our 4 colors - See web: www.lumavento.dk

I have attached logo and som old business Cards we have - Lets Make the new ones shine...:-) -

Industry/Entity Type

Business

Requirements
Must have
• the logo with lumavento only,

```html
<!DOCTYPE html>
<html lang="da">
<head>
<meta charset="utf-8">
<title>Lumavento – visitkort</title>
<link rel="stylesheet" href="https://fonts.googleapis.com/css2?family=Open+Sans:wght@400;600&display=swap">
<style>
  :root {
    --lime: #8dc63f;
    --plum: #6b2a78;
    --magenta: #c8368a;
    --orange: #e5873c;
    --ink: #2b2b2b;
    --grey: #5a5a5a;
    --paper: #ffffff;
    --backdrop: #e4e4e4;
  }
  * { box-sizing: border-box; margin: 0; padding: 0; }
  html, body { width: 1105px; height: 1200px; overflow: hidden; }
  body {
    background: var(--backdrop);
    font-family: "Open Sans", Arial, sans-serif;
    position: relative;
  }
  .card {
    position: absolute;
    left: 196px;
    width: 720px;
    height: 413px;
    background: var(--paper);
    overflow: hidden;
  }
  .card--front { top: 145px; }
  .card--back { top: 602px; display: flex; }

  .stripe-row {
    position: absolute;
    left: 0; right: 0;
    height: 19px;
    display: flex;
    gap: 4px;
  }
  .stripe-row--top { top: 0; }
  .stripe-row--bottom { bottom: 0; }
  .stripe-row span { flex: 1; }
  .c-lime { background: var(--lime); }
  .c-plum { background: var(--plum); }
  .c-magenta { background: var(--magenta); }
  .c-orange { background: var(--orange); }

  .brand {
    position: absolute;
    left: 105px;
    top: 200px;
    width: 275px;
    text-align: center;
  }
  .brand__name {
    display: inline-flex;
    align-items: center;
    gap: 10px;
    font-size: 25px;
    letter-spacing: 2px;
    color: var(--ink);
    line-height: 1;
  }
  .brand__dot {
    width: 14px; height: 14px;
    border-radius: 50%;
    background: var(--lime);
  }
  .brand__rule {
    height: 3px;
    background: var(--lime);
    margin-top: 22px;
  }
  .brand__tagline {
    margin-top: 14px;
    font-size: 15px;
    color: var(--ink);
  }

  .contact {
    position: absolute;
    left: 405px;
    top: 84px;
    color: var(--grey);
  }
  .contact__name {
    font-size: 26px;
    font-weight: 600;
    color: var(--lime);
    line-height: 1.1;
  }
  .contact__title {
    font-size: 18px;
    color: var(--ink);
    margin-top: 2px;
  }
  .contact__address {
    font-style: normal;
    font-size: 18px;
    line-height: 28px;
    margin-top: 10px;
  }
  .contact__list {
    list-style: none;
    margin-top: 10px;
    font-size: 18px;
  }
  .contact__list li {
    display: flex;
    align-items: center;
    gap: 12px;
    height: 27px;
  }
  .contact__list svg { width: 17px; height: 17px; fill: var(--lime); flex: none; }

  .band { height: 100%; }
  .band--lime { width: 174px; background: var(--lime); }
  .band--plum { width: 178px; background: var(--plum); }
  .band--magenta { width: 182px; background: var(--magenta); }
  .band--orange { width: 186px; background: var(--orange); }
  .back-name {
    position: absolute;
    left: 0; right: 0;
    top: 175px;
    text-align: center;
    font-size: 46px;
    letter-spacing: 3px;
    color: var(--paper);
    line-height: 1;
  }
</style>
</head>
<body>

<section class="card card--front" aria-label="Visitkort forside">
  <div class="stripe-row stripe-row--top"><span class="c-lime"></span><span class="c-plum"></span><span class="c-magenta"></span><span class="c-orange"></span></div>

  <div class="brand">
    <div class="brand__name"><span class="brand__dot"></span>lumavento</div>
    <div class="brand__rule"></div>
    <p class="brand__tagline">medier til unge</p>
  </div>

  <div class="contact">
    <h1 class="contact__name">Maren Holmsted</h1>
    <p class="contact__title">Salgsdirektør</p>
    <address class="contact__address">Solsikkevej 14<br>2100 Østerbro</address>
    <ul class="contact__list">
      <li><svg viewBox="0 0 24 24" aria-hidden="true"><path d="M6.6 10.8a15 15 0 0 0 6.6 6.6l2.2-2.2c.3-.3.7-.4 1-.2 1.1.4 2.3.6 3.6.6.6 0 1 .4 1 1V20c0 .6-.4 1-1 1A17 17 0 0 1 3 4c0-.6.4-1 1-1h3.5c.6 0 1 .4 1 1 0 1.3.2 2.5.6 3.6.1.3 0 .7-.2 1z"/></svg>+45 31 42 67 18</li>
      <li><svg viewBox="0 0 24 24" aria-hidden="true"><path d="M6.6 10.8a15 15 0 0 0 6.6 6.6l2.2-2.2c.3-.3.7-.4 1-.2 1.1.4 2.3.6 3.6.6.6 0 1 .4 1 1V20c0 .6-.4 1-1 1A17 17 0 0 1 3 4c0-.6.4-1 1-1h3.5c.6 0 1 .4 1 1 0 1.3.2 2.5.6 3.6.1.3 0 .7-.2 1z"/></svg>+45 52 73 19 40</li>
      <li><svg viewBox="0 0 24 24" aria-hidden="true"><path d="M2 5h20v14H2z M2 5l10 8 10-8" stroke="#fff" stroke-width="1.6"/></svg>mh@lumavento.dk</li>
      <li><svg viewBox="0 0 24 24" aria-hidden="true"><circle cx="12" cy="12" r="10"/><path d="M2 12h20M12 2c3 3 3 17 0 20M12 2c-3 3-3 17 0 20" stroke="#fff" stroke-width="1.4" fill="none"/></svg>www.lumavento.dk</li>
    </ul>
  </div>

  <div class="stripe-row stripe-row--bottom"><span class="c-lime"></span><span class="c-plum"></span><span class="c-magenta"></span><span class="c-orange"></span></div>
</section>

<section class="card card--back" aria-label="Visitkort bagside">
  <div class="band band--lime"></div>
  <div class="band band--plum"></div>
  <div class="band band--magenta"></div>
  <div class="band band--orange"></div>
  <div class="back-name">lumavento</div>
</section>

</body>
</html>
```